Modern business card design for professional copywriter

I'd like a business card design that I can use to have my cards printed out by quillprint.com as a squared corners business card (see artwork and design guidelines here: https://help.quillprint.com/hc/en-gb/sections/200570950-QUILL-Product-Templates)

The design should be clean and modern and reflect the colours, tone and branding on my website: https://tessavorrin.com.au

Target Market(s)

Professionals, B2B small business owners

Industry/Entity Type

Business

Contact Information for Business Card

Tessa Vorrin
m: 0468 905 327
e: tessa@tessavorrin.com.au
w: tessavorrin.com.au

Font styles to use
Sans Serif

Requirements
Must have
• Tagline: "Smart copywriting for clever business people"
• Brand colours: fd8000, 009984, 666666 and black
Nice to have

```html
<!DOCTYPE html>
<html lang="en">
<head>
<meta charset="utf-8">
<title>Tessa Vorrin Copywriter – Business Card</title>
<link rel="stylesheet" href="https://fonts.googleapis.com/css2?family=Lato:wght@400;700&family=Questrial&family=Tinos:ital,wght@1,700&display=swap">
<style>
  :root {
    --brand-orange: #f6842a;
    --brand-orange-deep: #ec7424;
    --brand-teal: #139b82;
    --brand-grey: #666666;
    --ink: #111111;
    --paper: #ffffff;
    --page-bg: #f2f2f2;
  }
  * { margin: 0; padding: 0; box-sizing: border-box; }
  html, body {
    width: 1200px; height: 586px; overflow: hidden;
    background: var(--page-bg);
  }
  .canvas { position: relative; width: 1200px; height: 586px; }

  .card {
    position: absolute; top: 129px;
    width: 502px; height: 301px;
    overflow: hidden;
  }
  .card--front { left: 62px; }
  .card--back { left: 619px; background: var(--paper); }

  /* Front */
  .front-texture {
    position: absolute; inset: 0;
    background: linear-gradient(135deg, var(--brand-orange) 0%, var(--brand-orange-deep) 55%, var(--brand-orange) 100%);
  }
  .brand-name {
    position: absolute;
    font-family: "Questrial", sans-serif;
    font-weight: 400;
    white-space: nowrap;
    line-height: 1;
  }
  .brand-role {
    position: absolute;
    font-family: "Questrial", sans-serif;
    text-transform: uppercase;
    white-space: nowrap;
    line-height: 1;
  }
  .card--front .brand-name {
    right: 69px; top: 92px;
    font-size: 54px; color: var(--paper);
    letter-spacing: -0.5px;
  }
  .card--front .brand-role {
    right: 66px; top: 140px;
    font-size: 13px; letter-spacing: 6.3px; color: var(--paper);
  }
  .social-row {
    position: absolute; top: 201px; left: 200px;
    display: flex; gap: 10px;
  }
  .social-row span {
    width: 20px; height: 20px; border-radius: 50%;
    background: var(--paper);
  }
  .services {
    position: absolute; top: 234px; left: 0; width: 100%;
    display: grid;
    grid-template-columns: 250px 12px 1fr;
    row-gap: 3px;
    font-family: "Lato", sans-serif; font-weight: 700;
    font-size: 12px; line-height: 16px; color: var(--ink);
    letter-spacing: -0.2px;
  }
  .services .left { text-align: right; }
  .services .dot { text-align: center; color: var(--paper); }

  /* Back */
  .back-texture {
    position: absolute; inset: 0;
    background: linear-gradient(160deg, #ffffff 0%, #f6f6f6 100%);
  }
  .card--back .brand-name {
    right: 33px; top: 48px;
    font-size: 40px; color: var(--brand-teal);
    letter-spacing: -0.4px;
  }
  .card--back .brand-role {
    right: 30px; top: 82px;
    font-size: 10px; letter-spacing: 4.4px; color: var(--brand-grey);
  }
  .contact-list {
    position: absolute; left: 28px; top: 188px;
    list-style: none;
    font-family: "Lato", sans-serif; font-size: 13.5px; color: var(--ink);
  }
  .contact-list li {
    display: flex; align-items: center; gap: 8px;
    height: 20px; margin-bottom: 6px;
  }
  .contact-icon {
    width: 18px; height: 18px; border-radius: 50%;
    background: var(--brand-teal);
    display: flex; align-items: center; justify-content: center;
  }
  .website {
    position: absolute; left: 29px; top: 240px;
    font-family: "Lato", sans-serif; font-weight: 700;
    font-size: 13.5px; color: var(--brand-teal);
  }
  .band-teal {
    position: absolute; left: 0; top: 274px; width: 100%; height: 5px;
    background: var(--brand-teal);
  }
  .band-tagline {
    position: absolute; left: 0; top: 279px; width: 100%; height: 22px;
    background: var(--brand-orange);
    display: flex; align-items: center; justify-content: center;
    font-family: "Tinos", serif; font-style: italic; font-weight: 700;
    font-size: 12.5px; color: #1a1a1a;
  }
</style>
</head>
<body>
<main class="canvas">

  <section class="card card--front" aria-label="Card front">
    <div class="front-texture" role="img" aria-label="Orange faceted low-poly background texture"></div>
    <div class="brand-name">Tessa Vorrin</div>
    <div class="brand-role">Copywriter</div>
    <div class="social-row" aria-label="Social profiles">
      <span></span><span></span><span></span><span></span>
    </div>
    <div class="services">
      <span class="left">Legal Copywriting</span><span class="dot">•</span><span>SEO Copywriting</span>
      <span class="left">Small Business Copywriting</span><span class="dot">•</span><span>Feature Writing</span>
      <span class="left">Website Copywriting</span><span class="dot">•</span><span>Content Marketing</span>
    </div>
  </section>

  <section class="card card--back" aria-label="Card back">
    <div class="back-texture" role="img" aria-label="Subtle fine diagonal line texture"></div>
    <div class="brand-name">Tessa Vorrin</div>
    <div class="brand-role">Copywriter</div>
    <ul class="contact-list">
      <li>
        <span class="contact-icon">
          <svg width="10" height="10" viewBox="0 0 10 10" aria-hidden="true">
            <path d="M2 1.2c.4-.3.9-.2 1.1.2l.8 1.4c.2.4.1.8-.2 1l-.5.4c.4.9 1 1.6 1.9 2l.4-.5c.3-.3.7-.4 1-.2l1.4.8c.4.2.5.7.2 1.1l-.5.7c-.4.5-1.1.7-1.7.4C3.7 7.5 2.4 6.2 1.4 4c-.3-.6-.1-1.3.4-1.7z" fill="#fff"/>
          </svg>
        </span>
        0468 905 327
      </li>
      <li>
        <span class="contact-icon">
          <svg width="10" height="8" viewBox="0 0 10 8" aria-hidden="true">
            <rect x="0.6" y="0.6" width="8.8" height="6.8" fill="none" stroke="#fff" stroke-width="1.1"/>
            <path d="M0.8 0.9 5 4.4 9.2 0.9" fill="none" stroke="#fff" stroke-width="1.1"/>
          </svg>
        </span>
        tessa@tessavorrin.com.au
      </li>
    </ul>
    <div class="website">www.tessavorrin.com.au</div>
    <div class="band-teal"></div>
    <div class="band-tagline">Smart copywriting for clever business people</div>
  </section>

</main>
</body>
</html>
```